BOLD & MINIMALIST DESIGN NEEDED

We want a very bold but minimalistic business card design that is impactful and utilizes both sides of the business card. Our current logo is included for your use.

We want bold fonts and good use of negative space. We don't want the logo to overpower the design.

Target Market(s)

Professionals who are building new commercial buildings.

Industry/Entity Type

Construction

Contact Information for Business Card

Name, Title, email, office phone, cell phone, website

Font styles to use
Serif
Sans Serif

Requirements
Must have
• Bold design!

```html
<!DOCTYPE html>
<html lang="en">
<head>
<meta charset="utf-8">
<title>Summitline Design + Build — Business Card</title>
<link href="https://fonts.googleapis.com/css2?family=Montserrat:wght@400;500;700;800;900&display=swap" rel="stylesheet">
<style>
  :root {
    --stage: #2b2b2b;
    --green: #86c440;
    --green-deep: #3f7a2c;
    --green-light: #a9d774;
    --ink: #111111;
    --paper: #ffffff;
  }
  * { margin: 0; padding: 0; box-sizing: border-box; }
  html, body {
    width: 1200px; height: 689px; overflow: hidden;
    background: var(--stage);
    font-family: "Montserrat", Arial, sans-serif;
  }
  .canvas {
    position: relative; width: 1200px; height: 689px;
    display: flex; align-items: center; justify-content: center; gap: 40px;
  }
  .card {
    position: relative; width: 540px; height: 309px;
    border-radius: 22px; overflow: hidden;
  }

  /* Front side */
  .card-front {
    background: linear-gradient(120deg, var(--green-light) 0%, var(--green) 45%, var(--green) 100%);
    display: flex; flex-direction: column; align-items: center; justify-content: center;
  }
  .brand-front {
    display: flex; align-items: center; gap: 14px;
    color: var(--green-deep); font-weight: 900; font-size: 54px; letter-spacing: 1px;
  }
  .brand-mark { width: 30px; height: 30px; background: var(--green-deep); }
  .tagline-front {
    margin-top: 6px; padding-top: 6px; border-top: 2px solid var(--green-deep);
    color: var(--green-deep); font-weight: 500; font-size: 17px; letter-spacing: 10px;
  }

  /* Back side */
  .card-back { background: var(--paper); }
  .swoosh { position: absolute; inset: 0; width: 540px; height: 309px; }
  .brand-back {
    position: absolute; left: 30px; top: 124px;
    display: flex; flex-direction: column; align-items: flex-start;
  }
  .brand-name {
    display: flex; align-items: center; gap: 9px;
    color: var(--ink); font-weight: 900; font-size: 32px; letter-spacing: 0.5px;
  }
  .brand-name .brand-mark { width: 18px; height: 18px; background: var(--ink); }
  .tagline-back {
    margin-top: 3px; padding-top: 3px; border-top: 1.5px solid var(--ink);
    color: var(--ink); font-weight: 500; font-size: 11px; letter-spacing: 6.5px;
  }
  .person {
    position: absolute; right: 28px; top: 20px; text-align: right;
    padding-right: 10px; border-right: 6px solid var(--green);
  }
  .person-name { color: var(--green); font-weight: 800; font-size: 24px; letter-spacing: 1px; line-height: 1.15; }
  .person-title { color: var(--ink); font-weight: 500; font-size: 12px; letter-spacing: 1px; margin-top: 3px; }
  .contact {
    position: absolute; right: 24px; top: 150px; text-align: right;
    color: var(--paper); font-size: 12px; line-height: 1.55; font-weight: 500;
  }
  .contact .gap { height: 8px; }
  .contact-row { display: flex; align-items: center; justify-content: flex-end; gap: 7px; }
  .contact-row svg { width: 11px; height: 11px; fill: var(--green); flex: none; }
  .contact-row .spacer { width: 11px; }
</style>
</head>
<body>
<main class="canvas">
  <section class="card card-front" aria-label="Card front">
    <div class="brand-front"><span class="brand-mark"></span>SUMMITLINE</div>
    <div class="tagline-front">DESIGN + BUILD</div>
  </section>

  <section class="card card-back" aria-label="Card back">
    <svg class="swoosh" viewBox="0 0 540 309" aria-hidden="true">
      <path transform="translate(-16,-14)" d="M600,92 L540,92 C448,92 394,108 356,160 C322,208 292,290 150,309 L60,330" fill="none" stroke="#111111" stroke-width="4"/>
      <path transform="translate(-8,-7)" d="M600,92 L540,92 C448,92 394,108 356,160 C322,208 292,290 150,309 L60,330" fill="none" stroke="#86c440" stroke-width="6"/>
      <path d="M540,92 C448,92 394,108 356,160 C322,208 292,290 150,309 L540,309 Z" fill="#111111"/>
    </svg>

    <div class="brand-back">
      <div class="brand-name"><span class="brand-mark"></span>SUMMITLINE</div>
      <div class="tagline-back">DESIGN + BUILD</div>
    </div>

    <div class="person">
      <div class="person-name">RAVI MEHRA</div>
      <div class="person-title">OWNER-CEO</div>
    </div>

    <div class="contact">
      <div class="contact-row">Your address, City<span class="spacer"></span></div>
      <div class="contact-row">State, Zip 1234<span class="spacer"></span></div>
      <div class="gap"></div>
      <div class="contact-row">123 456 789
        <svg viewBox="0 0 24 24"><path d="M6.6 10.8a15 15 0 0 0 6.6 6.6l2.2-2.2a1 1 0 0 1 1-.25 11.4 11.4 0 0 0 3.6.57 1 1 0 0 1 1 1V20a1 1 0 0 1-1 1A17 17 0 0 1 3 4a1 1 0 0 1 1-1h3.5a1 1 0 0 1 1 1c0 1.25.2 2.45.57 3.6a1 1 0 0 1-.25 1z"/></svg>
      </div>
      <div class="contact-row">123 456 789
        <svg viewBox="0 0 24 24"><path d="M7 1h10a2 2 0 0 1 2 2v18a2 2 0 0 1-2 2H7a2 2 0 0 1-2-2V3a2 2 0 0 1 2-2zm0 3v14h10V4zm5 15.5a1 1 0 1 0 0 2 1 1 0 0 0 0-2z"/></svg>
      </div>
      <div class="contact-row">info@yourmail.com
        <svg viewBox="0 0 24 24"><path d="M2 5h20v14H2zm2 2v.5l8 5 8-5V7zm0 3v7h16v-7l-8 5z"/></svg>
      </div>
      <div class="contact-row">www.yourwebsite.com
        <svg viewBox="0 0 24 24"><path d="M12 2a10 10 0 1 0 0 20 10 10 0 0 0 0-20zm0 2c.9 1.2 1.6 2.6 2 4h-4c.4-1.4 1.1-2.8 2-4zM4.3 14a8 8 0 0 1 0-4h3.4a16 16 0 0 0 0 4zm.8 2h3a14 14 0 0 0 1.3 3.5A8 8 0 0 1 5.1 16zm3-8h-3a8 8 0 0 1 4.3-3.5A14 14 0 0 0 8.1 8zM12 20c-.9-1.2-1.6-2.6-2-4h4c-.4 1.4-1.1 2.8-2 4zm2.3-6H9.7a14 14 0 0 1 0-4h4.6a14 14 0 0 1 0 4zm.3 5.5A14 14 0 0 0 15.9 16h3a8 8 0 0 1-4.3 3.5zm1.7-5.5a16 16 0 0 0 0-4h3.4a8 8 0 0 1 0 4z"/></svg>
      </div>
    </div>
  </section>
</main>
</body>
</html>
```